BQR, LLC Original

I need a business card design for a new company in Gaithersburg, MD. Though the name of the company is Wiremasters Of Northfield (BQR) we specialize in commercial kitchen ventilation systems as a complete turnkey project or as a service provider. We can design the entire system including the hoods, fans, ductwork, and fire system. We also specialize in fire alarm service, design, install and inspection. We are experts on any Ventaro Dynamics equipment including Pulsar VXM, Pulsar Canopies, EMS controls, Standard controls, PCU filtration and Make-up Air units with heaters and cooling. We can repair/retrofit old water wash hood systems as well. We are experts with local code requirements and upgrades.

Industry/Entity Type

Business

Contact Information for Business Card

Dale Pruitt, Wiremasters Of Northfield, LLC; 240-555-0187 Cell, Larkmoor, MD 20899. Dalep@wiremastersnorthfield.example

```html
<!DOCTYPE html>
<html lang="en">
<head>
<meta charset="utf-8">
<title>Wiremasters Of Northfield, LLC — Business Card</title>
<link rel="stylesheet" href="https://fonts.googleapis.com/css2?family=Cinzel:wght@400;500&family=Arimo:wght@400&display=swap">
<style>
  :root {
    --canvas-bg: #e9e6e1;
    --card-yellow: #f8d20c;
    --card-black: #0a0c14;
    --ink: #111111;
    --gold: #c7a02a;
    --shadow: 0 10px 28px rgba(0, 0, 0, 0.22);
  }
  * { margin: 0; padding: 0; box-sizing: border-box; }
  html, body {
    width: 1200px;
    height: 848px;
    overflow: hidden;
    background: var(--canvas-bg);
  }
  .canvas {
    width: 1200px;
    height: 848px;
    display: flex;
    flex-direction: column;
    align-items: center;
    justify-content: center;
    gap: 52px;
  }
  .card {
    position: relative;
    width: 600px;
    height: 343px;
    box-shadow: var(--shadow);
    overflow: hidden;
  }

  /* Front side */
  .card-front { background: var(--card-yellow); color: var(--ink); }
  .identity {
    position: absolute;
    left: 56px;
    top: 58px;
  }
  .person-name {
    font-family: "Cinzel", serif;
    font-weight: 500;
    font-size: 28px;
    letter-spacing: 0.5px;
    line-height: 1;
  }
  .company-line {
    font-family: "Arimo", sans-serif;
    font-size: 18px;
    margin-top: 4px;
    margin-left: 6px;
  }
  .brand-mark {
    position: absolute;
    right: 60px;
    top: 46px;
    display: flex;
    align-items: center;
    gap: 14px;
  }
  .brand-dot {
    width: 26px;
    height: 26px;
    border-radius: 50%;
    background: var(--ink);
  }
  .brand-name {
    font-family: "Cinzel", serif;
    font-weight: 500;
    font-size: 46px;
    letter-spacing: 2px;
    color: var(--ink);
  }
  .contact-list {
    position: absolute;
    left: 56px;
    bottom: 46px;
    list-style: none;
    font-family: "Arimo", sans-serif;
    font-size: 19px;
  }
  .contact-item {
    display: flex;
    align-items: center;
    gap: 14px;
    height: 32px;
  }
  .contact-icon { width: 22px; height: 22px; flex: none; }
  .contact-icon path, .contact-icon rect, .contact-icon circle { fill: var(--ink); }

  /* Back side */
  .card-back { background: var(--card-black); }
  .edge-band {
    position: absolute;
    left: 0;
    right: 0;
    height: 16px;
    background: var(--card-yellow);
  }
  .edge-band-top { top: 0; }
  .edge-band-bottom { bottom: 0; }
  .back-title {
    position: absolute;
    inset: 0;
    display: flex;
    align-items: center;
    justify-content: center;
    font-family: "Cinzel", serif;
    font-size: 24px;
    letter-spacing: 1.5px;
    color: var(--gold);
  }
</style>
</head>
<body>
<main class="canvas">

  <section class="card card-front" aria-label="Business card front">
    <div class="identity">
      <h1 class="person-name">Dale Pruitt</h1>
      <p class="company-line">Wiremasters</p>
    </div>

    <div class="brand-mark">
      <span class="brand-dot" aria-hidden="true"></span>
      <span class="brand-name">BQR</span>
    </div>

    <ul class="contact-list">
      <li class="contact-item">
        <svg class="contact-icon" viewBox="0 0 24 24" aria-hidden="true">
          <path d="M2 9c0-3 4-5 10-5s10 2 10 5v2h-5V8.5c-1.5-.6-3.2-.9-5-.9s-3.5.3-5 .9V11H2z"/>
          <rect x="5" y="12" width="14" height="8" rx="1.5"/>
        </svg>
        <span>240-555-0187</span>
      </li>
      <li class="contact-item">
        <svg class="contact-icon" viewBox="0 0 24 24" aria-hidden="true">
          <path d="M12 1.5a7 7 0 0 0-7 7c0 5 7 13.5 7 13.5s7-8.5 7-13.5a7 7 0 0 0-7-7zm0 9.8a2.8 2.8 0 1 1 0-5.6 2.8 2.8 0 0 1 0 5.6z"/>
        </svg>
        <span>Larkmoor, MD 20899.</span>
      </li>
      <li class="contact-item">
        <svg class="contact-icon" viewBox="0 0 24 24" aria-hidden="true">
          <path d="M2 5h20v14H2zM3.5 6.5v.4L12 13l8.5-6.1v-.4zM3.5 8.8v8.7h17V8.8L12 15z"/>
        </svg>
        <span>Dalep@wiremastersnorthfield.example</span>
      </li>
    </ul>
  </section>

  <section class="card card-back" aria-label="Business card back">
    <div class="edge-band edge-band-top"></div>
    <p class="back-title">Of Northfield, LLC</p>
    <div class="edge-band edge-band-bottom"></div>
  </section>

</main>
</body>
</html>
```